institute for female grief councelors needs a design for its facebook group

Each year about 350.000 German women do have a misscarriage while they are pregnant. Their pain and grief is soul deep. Lots of them are stay still in grief even if they have got other children who are healthy and alive. Lots of these women have got difficulty in finally letting go pain, rage and grief. Some are even still in grief after more than twenty or thirty years of having lost their child through misscarriage!!!!

With this facebook group I want to give hope, trust and support as well as helpful advice in coping with this deep soul pain after having lost your child through misscarriage.

The facebook cover shall cause a great curiosity and fascination to the mothers so that they are interested in joining our facebook group.

At our institute women can book a-one-year-training to become a certified "Coach for BirkenFeen" (grief councelor for women who are in deep grief after their misscarriage).

In Germany children who died through misscarriage are named "Sternenkind" (STARCHILD).
Therefore I want to have at least one shing star at the facebook cover symbolizing the still shining soullight of the dead child watching its mother who is still living on earth.

On the left side of the uploaded file you see the planet venus: symbol for mothers / female side of life.
The red sky colour symbolizes the colour of the uterus, the embryo's home before having died through misscarriage.
It ist also possible to include the silhoutte of a mother / several mothers looking up into the red / blue sky to watch the shining soullight of their dead child.

The facebook cover MUST include the following sentence:

Mama, ich lasse mein Licht für dich leuchten

(Mummy, I let my soullight shine for you)

Low design quality

Target Market(s)

German speaking mothers

Industry/Entity Type

coaching

Font styles to use
Script

Colors

Designer to choose colors to be used in the design.

Requirements
Must have
• golden fond writing, at least one shing star, silhouette of one / several mothers (no model typa - normal woman)
Nice to have
• planet venus - red background cover (like uterus colour)
Should not have
• mothers who like like a model or filmstar

```html
<!DOCTYPE html>
<html lang="de">
<head>
<meta charset="utf-8">
<title>Sternenkind – Facebook Cover</title>
<link rel="stylesheet" href="https://fonts.googleapis.com/css2?family=Dancing+Script:wght@700&family=Montserrat:wght@700&display=swap">
<style>
  :root{
    --space-deep:#0b0714;
    --space-violet:#2a1538;
    --space-plum:#4a1a3a;
    --nebula-red:#b8382a;
    --nebula-orange:#e0663a;
    --glow-core:#fff6e8;
    --planet-light:#f4dca6;
    --planet-mid:#e2b86c;
    --planet-dark:#c08a3e;
    --silhouette:#050305;
    --gold-light:#f6d98a;
    --gold:#d7a94a;
    --gold-dark:#a9761f;
    --button-bg:#ffffff;
    --sparkle:#ffffff;
  }
  *{margin:0;padding:0;box-sizing:border-box}
  html,body{width:1200px;height:676px;overflow:hidden;background:var(--space-deep)}
  .cover{position:relative;width:1200px;height:676px;overflow:hidden}
  .sky{
    position:absolute;inset:0;
    background:
      radial-gradient(circle at 80% 18%, rgba(184,56,42,.75) 0%, rgba(74,26,58,.55) 28%, transparent 55%),
      radial-gradient(ellipse at 10% 70%, rgba(184,56,42,.35) 0%, transparent 35%),
      linear-gradient(160deg, var(--space-violet) 0%, var(--space-deep) 55%, #120a1c 100%);
  }
  .star-glow{
    position:absolute;left:886px;top:51px;width:160px;height:140px;
    background:radial-gradient(ellipse at center, var(--glow-core) 0%, rgba(255,210,170,.85) 18%, rgba(224,102,58,.45) 45%, transparent 72%);
    border-radius:50%;
  }
  .sparkles{position:absolute;left:1010px;top:36px;width:130px;height:100px}
  .planet{
    position:absolute;left:70px;top:124px;width:512px;height:512px;border-radius:50%;
    background:
      radial-gradient(circle at 40% 35%, var(--planet-light) 0%, var(--planet-mid) 55%, var(--planet-dark) 100%);
  }
  .mother{
    position:absolute;left:278px;top:348px;width:271px;height:328px;
    background:linear-gradient(180deg, rgba(5,3,5,.0) 0%, var(--silhouette) 22%, var(--silhouette) 100%);
    border-radius:50% 50% 0 0 / 22% 22% 0 0;
  }
  .message{
    position:absolute;left:540px;top:420px;width:610px;text-align:center;
    font-family:"Dancing Script",cursive;font-weight:700;line-height:1.3;
    background:linear-gradient(180deg,var(--gold-light) 0%,var(--gold) 55%,var(--gold-dark) 100%);
    -webkit-background-clip:text;background-clip:text;color:transparent;
  }
  .message .salutation{display:block;font-size:42px;padding-left:10px}
  .message .line{display:block;font-size:42px;white-space:nowrap}
  .cta{position:absolute;left:738px;top:551px;display:flex;align-items:center;gap:14px}
  .cta .heart{width:28px;height:26px}
  .join-button{
    display:inline-flex;align-items:center;justify-content:center;
    width:139px;height:34px;border-radius:8px;background:var(--button-bg);
    font-family:"Montserrat",sans-serif;font-weight:700;font-size:20px;letter-spacing:.5px;
    color:var(--gold-dark);text-decoration:none;
  }
</style>
</head>
<body>
<main class="cover">
  <div class="sky" role="img" aria-label="Sternenhimmel mit roter Nebelwolke"></div>
  <div class="star-glow" role="img" aria-label="Leuchtender Stern als Seelenlicht des Sternenkindes"></div>
  <svg class="sparkles" viewBox="0 0 130 100" aria-hidden="true">
    <path d="M47 10 Q50 44 84 48 Q50 52 47 86 Q44 52 10 48 Q44 44 47 10Z" fill="var(--sparkle)"/>
    <path d="M82 12 Q83 22 92 23 Q83 24 82 34 Q81 24 72 23 Q81 22 82 12Z" fill="var(--sparkle)"/>
    <path d="M100 52 Q102 67 116 69 Q102 71 100 86 Q98 71 84 69 Q98 67 100 52Z" fill="var(--sparkle)"/>
  </svg>
  <div class="planet" role="img" aria-label="Planet Venus in goldgelben Tönen"></div>
  <div class="mother" role="img" aria-label="Silhouette einer Mutter mit wehendem Haar, die zum Stern hinaufblickt"></div>

  <h1 class="message">
    <span class="salutation">Mama,</span>
    <span class="line">ich lasse mein Licht für dich leuchten</span>
  </h1>

  <div class="cta">
    <svg class="heart" viewBox="0 0 28 26" aria-hidden="true">
      <defs>
        <linearGradient id="heartGold" x1="0" y1="0" x2="0" y2="1">
          <stop offset="0" stop-color="var(--gold-light)"/>
          <stop offset="1" stop-color="var(--gold-dark)"/>
        </linearGradient>
      </defs>
      <path d="M14 25 C6 18 1 13 1 8 A6.5 6.5 0 0 1 14 5 A6.5 6.5 0 0 1 27 8 C27 13 22 18 14 25Z" fill="url(#heartGold)"/>
    </svg>
    <a class="join-button" href="#">JOIN NOW</a>
  </div>
</main>
</body>
</html>
```